Website: BrightHarbor Business Consultants, Qianhai SEZ, China

Our client is a business consultancy firm and will be the first to set up in the Qianhai Shenzhen-Hong Kong Modern Service Industry Cooperation Zone, China So we need a corporate website concept that engages service, finance and technology sector companies. The company can provide all the necessary services needed to set up shop in Qianhai. They are looking for a modern, international, reliable and strong image.

Here are some websites for reference prupose:

http://www.vornelpax.com/ (we like the dynamic banner and clear, clean layout of this website)

http://www.quilbrenadvisory.com/ (we like the background city image, use of light font, hover over menu functions and color scheme - purple and grey)

http://www.dovu.com/ (we like the simplicity of this website, clear lines and we like the dynamic banner)
Updates

Hello, We are currently undecided between three logo designs.  All three have been uploaded to the design brief so that you can use them as reference for the website design. Thx

Also please take note of the addition menu selection 'About Qianhai'. Thx

Hello all Designers, First of all we want thank you for participating in our website competition, the calibre of design was high and we appreciated the expedience. Our company is Lumen Harvest Web Design and Internet Marketing based in Shenzhen, China. We anticipate rapid growth in the Chinese domestic market as the country shifts in to a service sector economy. We hope to continue building reliable working relationships with you based on idea sharing and constructive feedback. Once again, Thankyou, LH Team

Target Market(s)

International finance and technology companies looking to set up in Qianhai Special Economic Zone, China

Industry/Entity Type

Finance

Requirements
Must have
• Initial design for home page and in later selection stages a secondary page will be required.

The design should be for PSD concepts only no code!

Menu bar, Photo banner -
A. Photo banner and text overlay,
B.Photo Banner and text description to left or right.

Social Connect icons, Site search bar (top right), Logo space (top left).

Menu bar at top with Home, About Us, About Qianhai, Services, Portfolio, Partners, Our Team Contact Us.

Standard 3-4 box layout - Banner at top and 2-3 boxes under banner.

Colour scheme- A. Purple and Blue, must have light background/body
B. Shades of white, black and grey.

Simple, clear, clean, sharp.

```html
<!DOCTYPE html>
<html lang="en">
<head>
<meta charset="utf-8">
<title>BrightHarbor Business Consultants</title>
<link href="https://fonts.googleapis.com/css2?family=Source+Sans+3:ital,wght@0,300;0,400;0,600;1,400&display=swap" rel="stylesheet">
<style>
:root{
  --page:#f1f1f1;
  --magenta:#c5179b;
  --blue:#1683b0;
  --ink:#2c2c2c;
  --text:#4c4c4c;
  --nav-top:#565a6b;
  --nav-bottom:#2f3343;
  --tab-grey:#55565c;
  --line:#d6d6d6;
  --footer:#8d8d8d;
}
*{margin:0;padding:0;box-sizing:border-box}
html,body{width:1185px;height:1200px;overflow:hidden}
body{background:var(--page);font-family:"Source Sans 3",sans-serif;color:var(--text);position:relative}
.abs{position:absolute}
/* header */
.brand{left:178px;top:18px;width:180px}
.brand-mark{width:34px;height:34px;border-radius:50%;background:var(--magenta);margin:0 0 6px 70px}
.brand-name{font-size:19px;font-weight:300;letter-spacing:2.5px;color:var(--ink);line-height:1}
.brand-sub{font-size:7px;letter-spacing:1.6px;color:var(--ink);margin:3px 0 0 40px}
.social{left:886px;top:34px;display:flex;gap:18px}
.social span{width:14px;height:14px;border-radius:50%;background:#9a9a9a;display:block}
.search{left:843px;top:67px;width:164px;height:19px;border:1px solid #c9c9c9;background:#fff;font-size:7px;color:#666;padding:5px 8px}
.search svg{position:absolute;right:5px;top:3px}
/* nav */
.nav{left:178px;top:107px;width:829px;height:36px;background:linear-gradient(var(--nav-top),var(--nav-bottom));display:flex;align-items:center;font-size:10.5px;color:#fff}
.nav a{color:#fff;text-decoration:none;text-align:center;flex:1;white-space:nowrap}
.nav a.active{flex:0 0 74px;height:36px;line-height:36px;background:linear-gradient(#a3217f,#7c1868)}
/* banner */
.banner{left:178px;top:149px;width:829px;height:298px;display:flex}
.tab{width:32px;height:298px;background:var(--tab-grey);border-right:1px solid #6a6b71;position:relative}
.tab:nth-child(even){background:#606168}
.tab span{position:absolute;left:50%;bottom:16px;transform:translateX(-50%) rotate(-90deg);transform-origin:center;white-space:nowrap;font-size:13px;font-weight:300;color:#b9b9bd;width:0;display:flex;justify-content:flex-start}
.tab span b{font-weight:300;display:block}
.tab.current{background:var(--blue)}
.tab.current span{color:#fff;font-weight:400}
.hero{flex:1;height:298px;background:linear-gradient(180deg,#a9b7bf 0%,#c4cfd3 55%,#b6bbbd 100%);position:relative}
.hero-title{position:absolute;right:0;background:rgba(34,34,36,.9);color:#fff;font-weight:400;font-size:19.5px;padding:0 16px;height:34px;line-height:34px;white-space:nowrap}
.dots{position:absolute;right:10px;bottom:8px;display:flex;gap:3px}
.dots span{width:7px;height:7px;background:#d7d7d7}
.dots span:first-child{background:#fff}
/* news */
.news{left:178px;top:458px;width:829px;height:52px;background:#e4e4e4}
.news-label{position:absolute;left:0;top:0;width:144px;height:52px;background:var(--magenta);color:#fff;font-size:15px;line-height:52px;padding-left:25px;white-space:nowrap}
.news-text{position:absolute;left:160px;top:10px;width:500px;font-size:8.5px;line-height:16px;color:#444}
.btn{background:var(--blue);color:#fff;font-size:10px;display:flex;align-items:center;white-space:nowrap}
.news .btn{position:absolute;left:724px;top:10px;width:94px;height:31px;justify-content:center}
.rule{left:178px;width:829px;height:1px;background:var(--line)}
.section-title{color:var(--magenta);font-size:15px;font-weight:400;white-space:nowrap}
.arrows{display:flex;gap:4px}
.arrows span{width:14px;height:12px;background:#bbb;display:flex;align-items:center;justify-content:center}
/* portfolio */
.card{top:579px;width:260px}
.card-photo{height:113px;border:3px solid #e2e2e2;position:relative}
.card .btn{position:absolute;left:-3px;top:74px;height:24px}
.btn .lbl{padding:0 16px;line-height:24px;white-space:nowrap}
.btn .go{width:24px;height:24px;background:#2a2a2a;display:flex;align-items:center;justify-content:center;flex:0 0 24px}
.card h3{font-size:10.5px;font-weight:400;color:var(--ink);margin:17px 0 5px;white-space:nowrap}
.card p{font-size:9px;font-style:italic;line-height:16px;width:210px}
/* services */
.services{left:178px;top:802px;width:207px}
.services-head{height:26px;background:linear-gradient(90deg,#dde0e5,#eef0f2);padding-left:14px;line-height:26px;font-size:12px;color:var(--magenta)}
.services ul{list-style:none;margin:4px 0 0 3px;width:197px}
.services li{height:31px;line-height:31px;font-size:8.5px;color:#555;border-bottom:1px solid var(--line);padding-left:17px;position:relative;white-space:nowrap}
.services li:last-child{border:none}
.services li:before{content:"›";position:absolute;left:4px;top:-1px;font-size:12px;color:#aaa}
.about{left:415px;top:803px;width:460px}
.about p{font-size:8.6px;line-height:15.2px;margin-top:11px;color:#4a4a4a}
.about .btn{margin-top:16px;width:101px;height:24px;font-size:10px}
.about .btn .lbl{padding:0 0 0 14px;flex:1}
.bulbs{left:889px;top:825px;width:114px;height:123px;border-radius:50% 50% 30% 30%;background:radial-gradient(circle at 50% 35%,#d9ecf5,#a8c4d2 55%,rgba(241,241,241,0) 72%)}
/* partners */
.partners{left:178px;top:1020px;width:829px;height:64px;background:#fff;border:1px solid #dadada;display:flex;align-items:center;justify-content:space-around}
.partner{display:flex;align-items:center;gap:5px;font-size:14px;font-weight:600;white-space:nowrap}
.partner i{width:10px;height:10px;display:block}
/* footer */
.footer{left:178px;top:1105px;width:829px;height:48px;background:var(--footer);color:#fff;font-size:7.5px;display:flex;align-items:center;padding:0 20px;white-space:nowrap}
.footer nav{display:flex}
.footer nav a{color:#fff;text-decoration:none}
.footer nav a:after{content:"|";margin:0 13px}
.footer nav a:last-child:after{content:""}
.footer .copy{margin-left:auto}
</style>
</head>
<body>

<header>
  <div class="abs brand">
    <div class="brand-mark"></div>
    <div class="brand-name">BRIGHTHARBOR</div>
    <div class="brand-sub">BUSINESS CONSULTING</div>
  </div>
  <div class="abs social" aria-label="Social links"><span></span><span></span><span></span><span></span></div>
  <div class="abs search">SEARCH :
    <svg width="12" height="12" viewBox="0 0 12 12"><circle cx="5" cy="5" r="3.5" fill="none" stroke="#aaa" stroke-width="1.2"/><line x1="7.5" y1="7.5" x2="11" y2="11" stroke="#aaa" stroke-width="1.5"/></svg>
  </div>
  <nav class="abs nav">
    <a class="active" href="#">HOME</a><a href="#">ABOUT US</a><a href="#">ABOUT QIANHAI</a><a href="#">SERVICES</a><a href="#">PORTFOLIO</a><a href="#">PARTNERS</a><a href="#">OUR TEAM</a><a href="#">CONTACT US</a>
  </nav>
</header>

<section class="abs banner">
  <div class="tab"><span><b>CORPORATE FINANCE/RESTRUCTURINGV</b></span></div>
  <div class="tab"><span><b>RESTRUCTURING/TURNAROUND SERVICES</b></span></div>
  <div class="tab"><span><b>BANKRUPTCY SUPPORT SERVICES</b></span></div>
  <div class="tab"><span><b>TRANSACTION ADVISORY SERVICES</b></span></div>
  <div class="tab current"><span><b>PRIVATE EQUITY</b></span></div>
  <div class="hero" role="img" aria-label="Businessman leaping with a briefcase in front of city towers">
    <div class="hero-title" style="top:145px">BRIGHTHARBOR</div>
    <div class="hero-title" style="top:188px">BUSINESS CONSULTING</div>
    <div class="dots"><span></span><span></span><span></span><span></span></div>
  </div>
</section>

<section class="abs news">
  <div class="news-label">LATEST NEWS</div>
  <p class="news-text">LOREM IPSUM IS SIMPLY DUMMY TEXT OF THE PRINTING AND TYPESETTING INDUSTRY. LOREM IPSUM HAS BEEN THE INDUSTRY'S STANDARD DUMMY TEXT EVER SINCE THE 1500S</p>
  <div class="btn">READ HERE</div>
</section>

<div class="abs rule" style="top:526px"></div>

<h2 class="abs section-title" style="left:181px;top:543px">RECENT PORTFOLIO</h2>
<div class="abs arrows" style="left:974px;top:553px">
  <span><svg width="6" height="8"><path d="M5 1 2 4l3 3" fill="none" stroke="#fff" stroke-width="1.5"/></svg></span>
  <span><svg width="6" height="8"><path d="M1 1l3 3-3 3" fill="none" stroke="#fff" stroke-width="1.5"/></svg></span>
</div>

<article class="abs card" style="left:181px">
  <div class="card-photo" role="img" aria-label="Colleagues smiling in a bright office meeting" style="background:linear-gradient(120deg,#cdd6de,#8fa0b0 60%,#e5e9ee)">
    <div class="btn"><span class="lbl">CLICK HERE</span><span class="go"><svg width="10" height="8"><path d="M1 1l3 3-3 3M5 1l3 3-3 3" fill="none" stroke="#fff" stroke-width="1.4"/></svg></span></div>
  </div>
  <h3>LOREM IPSUM IS SIMPLY DUMMY TEXT</h3>
  <p>Lorem Ipsum is simply dummy text of the printing and ypesetting.</p>
</article>
<article class="abs card" style="left:464px">
  <div class="card-photo" role="img" aria-label="Businessman on a phone call between city buildings" style="background:linear-gradient(160deg,#3d4856,#7f94a8 55%,#5b6675)">
    <div class="btn"><span class="lbl">CLICK HERE</span><span class="go"><svg width="10" height="8"><path d="M1 1l3 3-3 3M5 1l3 3-3 3" fill="none" stroke="#fff" stroke-width="1.4"/></svg></span></div>
  </div>
  <h3 style="margin-left:4px">LOREM IPSUM IS SIMPLY DUMMY TEXT</h3>
  <p style="margin-left:4px">Lorem Ipsum is simply dummy text of the printing and ypesetting.</p>
</article>
<article class="abs card" style="left:747px">
  <div class="card-photo" role="img" aria-label="Business handshake against a blue sky and glass tower" style="background:linear-gradient(150deg,#4a5a78,#6f93c9 50%,#a9c2e6)">
    <div class="btn"><span class="lbl">CLICK HERE</span><span class="go"><svg width="10" height="8"><path d="M1 1l3 3-3 3M5 1l3 3-3 3" fill="none" stroke="#fff" stroke-width="1.4"/></svg></span></div>
  </div>
  <h3 style="margin-left:2px">LOREM IPSUM IS SIMPLY DUMMY TEXT</h3>
  <p style="margin-left:2px">Lorem Ipsum is simply dummy text of the printing and ypesetting.</p>
</article>

<div class="abs rule" style="top:778px"></div>

<aside class="abs services">
  <div class="services-head">SERVICES</div>
  <ul><li>AEROSPACE &amp; DEFENSE</li><li>AGRICULTURE</li><li>AUTOMOTIVE</li><li>CONSTRUCTION</li></ul>
</aside>

<section class="abs about">
  <h2 class="section-title">WHO WE ARE</h2>
  <p>Lorem Ipsum is simply dummy text of the printing and typesetting industry. Lorem Ipsum has been the industry's standard dummy text ever since the 1500s, when an unknown printer took a galley of type and scrambled it to make a type specimen book. It has survived not only five centuries, but also the leap into electronic typesetting, remaining essentially unchanged. It was popularised in the 1960s with the release of Typeline sheets containing Lorem Ipsum passages, and more recently with desktop publishing software like Pagewell.</p>
  <div class="btn"><span class="lbl">READ MORE</span><span class="go"><svg width="10" height="8"><path d="M1 1l3 3-3 3M5 1l3 3-3 3" fill="none" stroke="#fff" stroke-width="1.4"/></svg></span></div>
</section>
<div class="abs bulbs" role="img" aria-label="Three light bulbs, the middle one glowing blue"></div>

<div class="abs rule" style="top:973px"></div>

<h2 class="abs section-title" style="left:178px;top:989px">PARTNERS</h2>
<div class="abs arrows" style="left:974px;top:995px">
  <span><svg width="6" height="8"><path d="M5 1 2 4l3 3" fill="none" stroke="#fff" stroke-width="1.5"/></svg></span>
  <span><svg width="6" height="8"><path d="M1 1l3 3-3 3" fill="none" stroke="#fff" stroke-width="1.5"/></svg></span>
</div>
<section class="abs partners">
  <div class="partner" style="color:#1f9a3a">NORVADA TELECOM</div>
  <div class="partner" style="color:#b56a5c">Pellow Cafe</div>
  <div class="partner" style="color:#333"><i style="background:#e8742a"></i>TARVIX</div>
  <div class="partner" style="color:#e2443d"><i style="background:#1c8d4a"></i>Quenmark</div>
  <div class="partner" style="color:#2a5bb0">Fundelo</div>
  <div class="partner" style="color:#333"><i style="background:#f08a1c;border-radius:50%"></i>OSTREVA</div>
</section>

<footer class="abs footer">
  <nav><a href="#">HOME</a><a href="#">ABOUT US</a><a href="#">ABOUT QIANHAI</a><a href="#">SERVICES</a><a href="#">PORTFOLIO</a><a href="#">PARTNERS</a><a href="#">OUR TEAM</a><a href="#">CONTACT US</a></nav>
  <span class="copy">COPYRIGHTS 2013 © BRIGHTHARBOR. ALL RIGHTS RESERVED</span>
</footer>

</body>
</html>
```